Tolbek cards

I want a simple business card that pops.
Logo on one side.
On side two i want.
"Are you thinking about a new building on your property, or renovating an existing structure? Contact".....
Owners Name: Dale Whitacre
Owners Phone number: 610-555-0187
Address:4076 Copper Ridge RD, Harlow Falls, PA 16890
Committed to Quality, Service, and Integrity

```html
<!DOCTYPE html>
<html lang="en">
<head>
<meta charset="utf-8">
<title>Tolbek Builders LLC – Business Card</title>
<link href="https://fonts.googleapis.com/css2?family=Montserrat:wght@400;500;700&display=swap" rel="stylesheet">
<style>
  :root {
    --backdrop: #9a9a9a;
    --card-dark: #141414;
    --card-light: #ffffff;
    --brand-brown: #5a3e2b;
    --band-brown: #432d1e;
    --ink: #333333;
    --logo-light: #e6e6e6;
  }
  * { margin: 0; padding: 0; box-sizing: border-box; }
  html, body {
    width: 1200px; height: 1108px; overflow: hidden;
    background: var(--backdrop);
    font-family: "Montserrat", sans-serif;
  }
  .stage { position: relative; width: 1200px; height: 1108px; }
  .card {
    position: absolute; left: 242px; width: 715px; height: 409px;
    border-radius: 28px; overflow: hidden;
  }
  .card--front { top: 119px; background: var(--card-dark); }
  .card--back { top: 580px; background: var(--card-light); color: var(--ink); }

  .front-brand {
    position: absolute; left: 0; right: 0; top: 132px; height: 146px;
    display: flex; align-items: center; justify-content: center; gap: 30px;
    color: var(--logo-light); font-weight: 700;
  }
  .front-brand__mark { width: 140px; height: 140px; background: var(--logo-light); }
  .front-brand__name { font-size: 80px; letter-spacing: 1px; line-height: 1; }

  .back-intro {
    position: absolute; top: 20px; left: 0; right: 0;
    text-align: center; font-size: 18px; line-height: 29px; letter-spacing: 0.4px;
  }
  .back-brand {
    position: absolute; left: 42px; top: 117px; width: 300px;
    display: flex; flex-direction: column; align-items: center;
    color: var(--brand-brown); font-weight: 700;
  }
  .back-brand__mark { width: 88px; height: 88px; background: var(--brand-brown); }
  .back-brand__name { font-size: 52px; line-height: 1; margin-top: 22px; }
  .back-brand__sub { font-size: 16px; letter-spacing: 1px; margin-top: 6px; }

  .divider {
    position: absolute; left: 349px; top: 117px; width: 2px; height: 176px;
    background: var(--band-brown);
  }
  .contact { position: absolute; left: 385px; top: 112px; }
  .contact__name { font-size: 30px; font-weight: 700; color: var(--brand-brown); line-height: 38px; }
  .contact__role { font-size: 17px; margin-top: 2px; letter-spacing: 0.5px; }
  .contact__address { font-size: 18px; line-height: 29px; margin-top: 24px; letter-spacing: 0.4px; }
  .contact__phone {
    display: flex; align-items: center; gap: 8px;
    font-size: 18px; margin-top: 22px; letter-spacing: 0.4px;
  }
  .contact__phone svg { width: 17px; height: 14px; }

  .tagline-band {
    position: absolute; left: 0; right: 0; top: 359px; height: 25px;
    background: var(--band-brown); color: #ffffff;
    display: flex; align-items: center; justify-content: center;
    font-size: 17px; letter-spacing: 0.4px;
  }
</style>
</head>
<body>
<main class="stage">
  <section class="card card--front" aria-label="Card front">
    <div class="front-brand">
      <span class="front-brand__mark"></span>
      <span class="front-brand__name">TOLBEK</span>
    </div>
  </section>

  <section class="card card--back" aria-label="Card back">
    <p class="back-intro">Are you thinking about a new building on your<br>property, or renovating an existing structure? Contact</p>

    <div class="back-brand">
      <span class="back-brand__mark"></span>
      <span class="back-brand__name">TOLBEK</span>
      <span class="back-brand__sub">BUILDERS LLC</span>
    </div>

    <div class="divider"></div>

    <div class="contact">
      <h1 class="contact__name">Dale Whitacre</h1>
      <p class="contact__role">Owner</p>
      <p class="contact__address">4076 Copper Ridge RD,<br>Harlow Falls, PA 16890</p>
      <p class="contact__phone">
        <svg viewBox="0 0 17 14" aria-hidden="true">
          <path d="M1 5 Q8.5 -1 16 5 L14 7 L11.5 5.5 L11.5 4 Q8.5 2.8 5.5 4 L5.5 5.5 L3 7 Z" fill="#333"/>
          <rect x="3.5" y="7" width="10" height="6" rx="1" fill="#333"/>
        </svg>
        610-555-0187
      </p>
    </div>

    <div class="tagline-band">Committed to Quality, Service, and Integrity</div>
  </section>
</main>
</body>
</html>
```